Business Card Design

I am an Event and Wedding Planner in need of an eye catching business card featuring my logo (attached), my contact details, and my company tagline (Making every celebration glow with wonder...) I would like the tagline in font similar the logo's font.
Updates
I have just noticed that my logo has a misspelling so for the final design, I will be uploading a corrected logo as soon as I have it.
My apologies.
Reason: Waiting on a corrected logo...Lantern is misspelled and it should say Weddings not Wedding
The logo has been corrected so now Lantern is spelled correctly and it says Weddings instead of Wedding. Please use Edwardian Script ITC as the font for the tagline so it will match the logo. Thank you for your patience.
Target Market(s)
Engaged couples and people hosting milestone celebrations. 25-50 years old, predominately female
Industry/Entity Type
Business
Contact Information for Business Card
Rosalind Merrow, Event Manager / Owner, Mobile: 0491 868 254, Email: rosalind@velvetlanternco.com.au, www.velvetlanternco.com.au, Making every celebration glow with wonder...

```html
<!DOCTYPE html>
<html lang="en">
<head>
<meta charset="utf-8">
<title>Velvet Lantern Co. – Business Card</title>
<link href="https://fonts.googleapis.com/css2?family=Arimo:wght@400&family=EB+Garamond:ital@1&family=Pinyon+Script&display=swap" rel="stylesheet">
<style>
  :root {
    --backdrop: #d4d4d4;
    --card-red: #c01f26;
    --ink: #111111;
    --paper: #ffffff;
    --band-black: #0d0d0d;
    --tag-red: #c01f26;
  }
  * { margin: 0; padding: 0; box-sizing: border-box; }
  html, body { width: 1200px; height: 1000px; overflow: hidden; }
  body { background: var(--backdrop); position: relative; }

  .card { position: absolute; width: 670px; height: 385px; overflow: hidden; box-shadow: 0 2px 6px rgba(0,0,0,.25); }
  .card-back { left: 148px; top: 75px; background: var(--card-red); }
  .card-front { left: 300px; top: 510px; background: var(--paper); }
  .band { position: absolute; left: 0; width: 100%; display: block; }
  .band-top { top: 0; }
  .band-bottom { bottom: 0; }

  .holder-name { position: absolute; left: 12px; top: 30px; font: 400 17px/1 "Arimo", sans-serif; color: var(--paper); letter-spacing: .3px; }
  .holder-title { position: absolute; left: 12px; top: 51px; font: italic 15px/1 "EB Garamond", serif; color: var(--ink); }

  .contact-list { position: absolute; left: 14px; top: 188px; list-style: none; }
  .contact-item { display: flex; align-items: center; height: 29px; font: 400 16px/1 "Arimo", sans-serif; color: var(--ink); }
  .contact-icon { width: 22px; height: 22px; margin-right: 12px; flex: none; }

  .brand-name { position: absolute; left: 0; width: 100%; top: 92px; text-align: center; font: 400 74px/1 "Pinyon Script", cursive; color: var(--ink); }
  .tagline-rule { position: absolute; left: 90px; width: 470px; top: 300px; height: 1px; background: linear-gradient(90deg, transparent, var(--tag-red) 30%, var(--tag-red) 70%, transparent); }
  .tagline { position: absolute; left: 0; width: 100%; top: 310px; text-align: center; font: 400 27px/1 "Pinyon Script", cursive; color: var(--tag-red); }
</style>
</head>
<body>

<section class="card card-back" aria-label="Card back with contact details">
  <svg class="band band-top" width="670" height="10" viewBox="0 0 670 10">
    <rect width="670" height="10" fill="var(--paper)"/>
    <path d="M430 0 H670 V10 H455 Q440 10 430 0 Z" fill="var(--band-black)"/>
  </svg>
  <p class="holder-name">ROSALIND MERROW</p>
  <p class="holder-title">Event Manager / Owner</p>
  <ul class="contact-list">
    <li class="contact-item">
      <svg class="contact-icon" viewBox="0 0 22 22"><rect x="1" y="5" width="20" height="13" fill="var(--ink)"/><path d="M1 5 L11 13 L21 5" fill="none" stroke="var(--card-red)" stroke-width="1.4"/></svg>
      rosalind@velvetlanternco.com.au
    </li>
    <li class="contact-item">
      <svg class="contact-icon" viewBox="0 0 22 22"><path d="M1 8 Q11 0 21 8 L19 11 L15 9 L15 7 Q11 5 7 7 L7 9 L3 11 Z" fill="var(--ink)"/><rect x="4" y="11" width="14" height="9" rx="1.5" fill="var(--ink)"/><circle cx="11" cy="15.5" r="2.4" fill="var(--card-red)"/></svg>
      0491 868 254
    </li>
    <li class="contact-item">
      <svg class="contact-icon" viewBox="0 0 22 22" fill="none" stroke="var(--ink)" stroke-width="1.4"><circle cx="11" cy="11" r="9.5"/><ellipse cx="11" cy="11" rx="4.5" ry="9.5"/><path d="M1.5 11 H20.5 M3.5 6 H18.5 M3.5 16 H18.5 M11 1.5 V20.5"/></svg>
      www.velvetlanternco.com.au
    </li>
  </ul>
  <svg class="band band-bottom" width="670" height="14" viewBox="0 0 670 14">
    <rect width="670" height="14" fill="var(--paper)"/>
    <path d="M440 0 H670 V14 H465 Q450 14 440 0 Z" fill="var(--band-black)"/>
  </svg>
</section>

<section class="card card-front" aria-label="Card front with company name and tagline">
  <svg class="band band-top" width="670" height="9" viewBox="0 0 670 9">
    <rect width="670" height="9" fill="var(--card-red)"/>
    <path d="M440 0 H670 V9 H462 Q450 9 440 0 Z" fill="var(--band-black)"/>
  </svg>
  <p class="brand-name">Velvet Lantern</p>
  <div class="tagline-rule"></div>
  <p class="tagline">Making every celebration glow with wonder...</p>
  <svg class="band band-bottom" width="670" height="20" viewBox="0 0 670 20">
    <rect width="670" height="20" fill="var(--card-red)"/>
    <path d="M420 0 H670 V20 H445 Q430 20 420 0 Z" fill="var(--band-black)"/>
  </svg>
</section>

</body>
</html>
```